Real estate broker business card

Want a modern celan but effective business card for my residential and commercial real estate business. I want the back of the card to advertise my services and to capture business. I have attached the back of my current business card fore ideas
Updates

Logos, photo and text updates added! Added Saturday, September 3, 2016

Project Deadline Extended Reason: LOGOS, PHOTOS AND TEST JUST UPLOADED! I'M READY TO PICK A DESIGN! THANK YOU! Added Saturday, September 3, 2016

Target Market(s)

home buyers and seller. commercial buyers and sellers

Industry/Entity Type

Real Estate

Contact Information for Business Card

must have my contact information and my photo

Requirements
Must have
• Carla Ventrino
• Owner & Qualifying Broker
• Ventrino Real Estate Services
• 505.718.2094
• carla@ventrinohomes.example
• www.ventrinohomes.example
Nice to have
• metallic
• Business capture text: " Don't buy or lease property without someone looking out for your best interests. I will represent you on your home or investment purchase for FREE!"
• "Home owners, call today to receive a FREE market analysis for your homes value!

```html
<!DOCTYPE html>
<html lang="en">
<head>
<meta charset="utf-8">
<title>Ventrino Real Estate Services – Business Card</title>
<link href="https://fonts.googleapis.com/css2?family=Source+Sans+3:ital,wght@0,400;0,600;0,700;1,400&display=swap" rel="stylesheet">
<style>
  :root {
    --stage: #e9e9ea;
    --teal: #0f6470;
    --ink: #1b1b1b;
    --ink-soft: #6a6e72;
    --silver-light: #f1f1f2;
    --silver-mid: #c9cbcd;
    --silver-dark: #6d7376;
  }
  * { box-sizing: border-box; margin: 0; padding: 0; }
  html, body { width: 1200px; height: 900px; overflow: hidden; }
  body {
    position: relative;
    background: var(--stage);
    font-family: "Source Sans 3", "Myriad Pro", sans-serif;
    color: var(--ink);
  }
  .card {
    position: absolute;
    overflow: hidden;
    box-shadow: 0 6px 18px rgba(0,0,0,0.18);
    background:
      linear-gradient(112deg,
        var(--silver-mid) 0%, var(--silver-dark) 9%, var(--silver-light) 22%,
        var(--silver-light) 45%, #dcdddf 60%, var(--silver-light) 100%);
  }
  .card-front { left: 237px; top: 61px; width: 556px; height: 344px; }
  .card-back  { left: 457px; top: 518px; width: 560px; height: 343px; }

  .front-accent {
    position: absolute; left: 310px; top: 0; width: 246px; height: 344px;
    background: linear-gradient(100deg, rgba(15,100,112,0) 0%, rgba(15,100,112,0.35) 40%, var(--teal) 75%);
  }

  .brand { position: absolute; color: var(--ink); font-weight: 600; line-height: 1; }
  .card-front .brand { left: 44px; top: 58px; }
  .brand-name { font-size: 44px; letter-spacing: 1px; }
  .brand-tag { font-size: 15px; letter-spacing: 2.6px; margin-top: 4px; }

  .agent { position: absolute; left: 46px; top: 158px; }
  .agent-name { font-size: 19px; font-weight: 600; line-height: 1.1; }
  .agent-title { font-size: 15px; margin-top: 1px; }

  .contact-list { position: absolute; left: 46px; top: 235px; list-style: none; }
  .contact-list li { display: flex; align-items: center; font-size: 15px; height: 20px; }
  .contact-list svg { width: 11px; height: 11px; margin-right: 10px; fill: var(--ink); }

  .back-brand { position: absolute; left: 33px; top: 48px; display: flex; align-items: center; }
  .back-brand .mark { width: 60px; height: 60px; background: var(--teal); margin-right: 14px; }
  .back-brand .brand-text { color: var(--teal); font-weight: 600; line-height: 1; }
  .back-brand .brand-name { font-size: 44px; letter-spacing: 1px; }
  .back-brand .brand-tag { font-size: 15px; letter-spacing: 2.4px; margin-top: 4px; }

  .pitch {
    position: absolute; left: 33px; top: 164px; width: 312px;
    font-size: 15px; line-height: 1.28; color: var(--teal); font-weight: 400;
  }
  .offer {
    position: absolute; left: 33px; top: 258px; width: 255px;
    font-size: 14.5px; line-height: 1.32; font-style: italic; color: var(--ink-soft);
  }
  .agent-photo {
    position: absolute; right: 0; top: 66px; width: 180px; height: 277px;
    border-radius: 90px 0 0 0;
    background: linear-gradient(180deg, #2a1d18 0%, #4a3328 45%, #c9a189 62%, #ece9e7 100%);
  }
</style>
</head>
<body>

<section class="card card-front" aria-label="Business card front">
  <div class="front-accent" role="img" aria-label="Decorative teal and silver accent area"></div>

  <div class="brand">
    <div class="brand-name">VENTRINO</div>
    <div class="brand-tag">REAL ESTATE SERVICES</div>
  </div>

  <div class="agent">
    <p class="agent-name">Carla Ventrino</p>
    <p class="agent-title">Owner &amp; Qualifying Broker</p>
  </div>

  <ul class="contact-list">
    <li><svg viewBox="0 0 24 24"><path d="M6.6 10.8a15 15 0 0 0 6.6 6.6l2.2-2.2a1 1 0 0 1 1-.25 11.4 11.4 0 0 0 3.6.57 1 1 0 0 1 1 1V20a1 1 0 0 1-1 1A17 17 0 0 1 3 4a1 1 0 0 1 1-1h3.5a1 1 0 0 1 1 1c0 1.25.2 2.45.57 3.57a1 1 0 0 1-.25 1z"/></svg>505.718.2094</li>
    <li><svg viewBox="0 0 24 24"><path d="M2 5h20v14H2z M4 7v.5l8 5 8-5V7l-8 5z" fill-rule="evenodd"/></svg>carla@ventrinohomes.example</li>
    <li><svg viewBox="0 0 24 24"><circle cx="12" cy="12" r="10"/></svg>www.ventrinohomes.example</li>
  </ul>
</section>

<section class="card card-back" aria-label="Business card back">
  <div class="back-brand">
    <div class="mark" aria-hidden="true"></div>
    <div class="brand-text">
      <div class="brand-name">VENTRINO</div>
      <div class="brand-tag">REAL ESTATE SERVICES</div>
    </div>
  </div>

  <p class="pitch">Don't buy or lease property without someone looking out for your best interests. I will represent you on your home or investment purchase for FREE!</p>
  <p class="offer">Home owners, call today to receive a FREE market analysis for your homes value!</p>

  <div class="agent-photo" role="img" aria-label="Portrait photo of the broker, Carla Ventrino"></div>
</section>

</body>
</html>
```